KVOR Individual and Corporate Development Business Card Design

KVOR needs a business card design that is aligned with it's values and targetted markets. Coherent Lattice of Adaptive Reasoning Method's self diagnosis model and tools, which can be used for personal improvement and team/business performance enhancement, is based on the learnings of over 20 years of medical practitioning. KVOR supercharges personal effectiveness and awareness to also increase team and business performance.

The targetted markets are high performance individuals and teams who aspire seek to enhance their capabilities and achieve their absolute best potential.

Look and feel for the business card design we are looking for is high technology, premium, fresh, new and medical.

Target Market(s)

Industry/Entity Type

Business Consultant

Contact Information for Business Card

Logo, Full Name, Title, Phone number, Email, company name, Address,

Font styles to use
Sans Serif

Requirements
Must have
• Tag line: Sharpening Clarity for Purposeful Leading Teams
• Please use same colours as the logo.

```html
<!DOCTYPE html>
<html lang="en">
<head>
<meta charset="utf-8">
<title>KVOR Business Card</title>
<link rel="stylesheet" href="https://fonts.googleapis.com/css2?family=Roboto+Condensed:wght@400;700&display=swap">
<style>
  :root {
    --teal: #1fb0c8;
    --teal-dark: #1795ab;
    --slate: #5a6068;
    --ink: #4a4f55;
    --rule: #c9cdd1;
    --paper: #f7f7f7;
    --stage: #e6e7e9;
    --white: #ffffff;
  }
  * { box-sizing: border-box; margin: 0; padding: 0; }
  html, body { width: 1200px; height: 911px; overflow: hidden; }
  body {
    background: var(--stage);
    font-family: "Roboto Condensed", Arial, sans-serif;
    position: relative;
  }
  .card {
    position: absolute;
    left: 330px;
    width: 540px;
    height: 310px;
    overflow: hidden;
    box-shadow: 0 6px 18px rgba(0,0,0,0.18);
  }
  .card--front { top: 110px; background: var(--paper); }
  .card--back  { top: 490px; background: var(--slate); }

  .brand { position: absolute; display: flex; flex-direction: column; }
  .brand__row { display: flex; align-items: center; gap: 10px; }
  .brand__mark { width: 18px; height: 18px; border-radius: 50%; }
  .brand__name { font-weight: 700; letter-spacing: 2px; line-height: 1; }
  .brand__full { font-weight: 700; text-transform: uppercase; line-height: 1.05; font-size: 12px; letter-spacing: .3px; margin-top: 6px; padding-top: 5px; }

  .card--front .brand { left: 34px; top: 92px; }
  .card--front .brand__name { font-size: 54px; color: var(--teal); }
  .card--front .brand__mark { background: var(--teal); }
  .card--front .brand__full { color: var(--teal); border-top: 1px solid var(--rule); width: 190px; }

  .divider { position: absolute; left: 0; top: 0; width: 540px; height: 250px; }

  .contact { position: absolute; left: 300px; top: 30px; color: var(--ink); font-size: 13px; line-height: 1.35; }
  .contact__name { color: var(--teal); font-size: 19px; font-weight: 700; text-transform: uppercase; line-height: 1.1; }
  .contact__title { font-size: 14px; text-transform: uppercase; margin-bottom: 12px; }
  .contact__address { margin-bottom: 8px; }
  .contact__line { display: flex; align-items: center; gap: 7px; }
  .contact__line svg { width: 11px; height: 11px; flex: none; }

  .band { position: absolute; left: 0; right: 0; bottom: 0; height: 42px; border-top: 6px solid #d8dbde; background: var(--teal); }
  .band__tagline { color: var(--white); font-size: 14px; line-height: 36px; padding-left: 48px; white-space: nowrap; }

  .card--back .brand { left: 50%; top: 50%; transform: translate(-50%, -50%); align-items: flex-start; }
  .card--back .brand__name { font-size: 66px; color: var(--white); }
  .card--back .brand__mark { background: var(--white); width: 22px; height: 22px; }
  .card--back .brand__full { color: var(--white); font-size: 14px; border-top: 1px solid #8a9097; width: 240px; }
</style>
</head>
<body>
  <section class="card card--front" aria-label="Business card front">
    <div class="brand">
      <div class="brand__row">
        <span class="brand__name">KVOR</span>
        <span class="brand__mark"></span>
      </div>
      <span class="brand__full">Coherent Lattice of<br>Adaptive Reasoning Method's</span>
    </div>

    <svg class="divider" viewBox="0 0 540 250" aria-hidden="true">
      <line x1="258" y1="20" x2="278" y2="220" stroke="#d2d5d8" stroke-width="1"/>
    </svg>

    <div class="contact">
      <p class="contact__name">Mara Ellison</p>
      <p class="contact__title">CEO/Founder</p>
      <p class="contact__address">Coherent Lattice of<br>Adaptive Reasoning Method<br>4120 Harbor View Road<br>Juneau, Alaska 34880</p>
      <p class="contact__line">
        <svg viewBox="0 0 12 12"><path d="M2.5 1 L4.5 1 L5.3 3.6 L4 4.6 C4.7 6 5.9 7.3 7.4 8 L8.4 6.7 L11 7.5 L11 9.5 C11 10.3 10.3 11 9.5 11 C5 11 1 7 1 2.5 C1 1.7 1.7 1 2.5 1 Z" fill="var(--teal)"/></svg>
        555 014 2290
      </p>
      <p class="contact__line">
        <svg viewBox="0 0 12 12"><rect x="1" y="2.5" width="10" height="7" fill="var(--teal)"/><path d="M1 2.5 L6 6.5 L11 2.5" fill="none" stroke="#fff" stroke-width="1"/></svg>
        hello@kvorlabs.com
      </p>
      <p class="contact__line">
        <svg viewBox="0 0 12 12"><circle cx="6" cy="6" r="5" fill="var(--teal)"/><path d="M1 6 H11 M6 1 C3.5 3.5 3.5 8.5 6 11 M6 1 C8.5 3.5 8.5 8.5 6 11" fill="none" stroke="#fff" stroke-width=".8"/></svg>
        www.kvorlabs.com
      </p>
    </div>

    <div class="band">
      <p class="band__tagline">Sharpening Clarity for Purposeful Leading Teams</p>
    </div>
  </section>

  <section class="card card--back" aria-label="Business card back">
    <div class="brand">
      <div class="brand__row">
        <span class="brand__name">KVOR</span>
        <span class="brand__mark"></span>
      </div>
      <span class="brand__full">Coherent Lattice of<br>Adaptive Reasoning Method's</span>
    </div>
  </section>
</body>
</html>
```